Business Card Design for my Real Estate Investing Company

This is for a Real Estate Investing Company that will be serving the Las Vegas Valley. Id like the following slogan included: "Investing in Our Community" I have attached my logo. You will see the color tones I'm interested in..in my logo. I would like the card to be double-sided with a modern, professional look.
Target Market(s)
Homeowners, banks, real estate industry
Industry/Entity Type
Real Estate
Contact Information for Business Card
name: Dale Harwick
position: Managing Member
address: 4821 Corliss Pkwy ste 207-300
N. Las Vegas, NV 89084
phone: (702) 555-0143
fax: (702) 555-0187
email: SummitRidgeEstate@hollowmail.test
web: SummitRidgeEstates.test
*At the bottom of the card I would like....
We buy houses for cash....no repairs, no commissions, no fees!
Logo Text
SUMMIT RIDGE ESTATES "Investing in Our Community"
Font styles to use
Other font styles liked:
- Lora
Requirements
Must have
- On the back of the card, i'd like to have my logo large and the following statements:
- Are you considering selling your home? Want a simple, hassle-free transaction? We can help! We buy houses for cash and can close quickly! No need to do any repairs, no realtor commissions, no closing costs.....and no headaches. Let us help you with your real estate needs...!
Nice to have
- multiple colors 2 two tone on front and back

```html
<!DOCTYPE html>
<html lang="en">
<head>
<meta charset="utf-8">
<title>Summit Ridge Estates – Business Card</title>
<link href="https://fonts.googleapis.com/css2?family=Lora:ital,wght@0,400;0,600;1,400&family=Questrial&display=swap" rel="stylesheet">
<style>
  :root {
    --page: #eceef1;
    --blue: #1f5fb0;
    --blue-deep: #164a94;
    --blue-light: #3d8ad6;
    --white: #ffffff;
    --grey: #6b6f76;
    --ink: #2a2e35;
  }
  * { margin: 0; padding: 0; box-sizing: border-box; }
  html, body { width: 1200px; height: 900px; overflow: hidden; background: var(--page); }
  .canvas { position: relative; width: 1200px; height: 900px; }

  .card {
    position: absolute;
    width: 525px; height: 300px;
    border-radius: 4px;
    overflow: hidden;
    box-shadow: 0 6px 18px rgba(0,0,0,.18);
  }

  /* Back of card */
  .card-back {
    left: 60px; top: 110px;
    background: linear-gradient(160deg, var(--blue-light) 0%, var(--blue) 45%, var(--blue-deep) 100%);
    color: var(--white);
    text-align: center;
    font-family: 'Lora', serif;
  }
  .back-pitch {
    margin: 30px auto 0;
    width: 440px;
    font-size: 13.5px;
    line-height: 1.42;
  }
  .back-brand { margin-top: 26px; }
  .back-brand .brand-name {
    font-size: 34px; font-weight: 600; letter-spacing: 1px; line-height: 1;
  }
  .back-brand .brand-slogan {
    margin-top: 8px; font-size: 14px; letter-spacing: 3px;
  }

  /* Front of card */
  .card-front {
    left: 615px; top: 490px;
    background: var(--white);
    font-family: 'Questrial', sans-serif;
  }
  .front-band { position: absolute; inset: 0; }
  .front-brand {
    position: absolute; right: 28px; top: 26px;
    text-align: right;
    font-family: 'Lora', serif;
    color: var(--blue);
  }
  .front-brand .brand-name { font-size: 19px; font-weight: 600; letter-spacing: .5px; }
  .front-brand .brand-slogan { font-size: 10px; letter-spacing: 2px; margin-top: 3px; }
  .holder { position: absolute; left: 30px; top: 100px; }
  .holder-name { color: var(--blue); font-size: 19px; letter-spacing: .5px; }
  .holder-role { color: var(--grey); font-size: 12.5px; margin-top: 2px; }
  .address {
    position: absolute; right: 28px; top: 142px;
    color: var(--white); font-size: 11.5px; line-height: 1.4; text-align: left;
  }
  .contacts {
    position: absolute; left: 30px; top: 178px;
    list-style: none; color: var(--white); font-size: 11.5px; line-height: 1.45;
  }
  .contacts li { display: flex; align-items: center; gap: 7px; }
  .contacts svg { width: 10px; height: 10px; fill: var(--white); flex: none; }
  .tagline {
    position: absolute; left: 0; right: 0; bottom: 14px;
    text-align: center; color: var(--blue);
    font-family: 'Lora', serif; font-style: italic; font-size: 15.5px;
  }
</style>
</head>
<body>
<div class="canvas">

  <section class="card card-back" aria-label="Back of business card">
    <p class="back-pitch">
      Are you considering selling your home?<br>
      Want a simple, hassle-free transaction?<br>
      We can help! We buy houses for cash and can close quickly!<br>
      No need to do any repairs, no realtor commissions,<br>
      no closing costs.....and no headaches.<br>
      Let us help you with your real estate needs...!
    </p>
    <div class="back-brand">
      <div class="brand-name">SUMMIT RIDGE ESTATES</div>
      <div class="brand-slogan">"Investing in Our Community"</div>
    </div>
  </section>

  <section class="card card-front" aria-label="Front of business card">
    <svg class="front-band" viewBox="0 0 525 300" preserveAspectRatio="none" aria-hidden="true">
      <defs>
        <linearGradient id="bandFill" x1="0" y1="0" x2="1" y2="0">
          <stop offset="0" stop-color="#164a94"/>
          <stop offset="0.5" stop-color="#2a6fc0"/>
          <stop offset="1" stop-color="#1f5fb0"/>
        </linearGradient>
      </defs>
      <polygon points="0,172 130,172 150,160 525,124 525,250 0,250" fill="url(#bandFill)"/>
      <polygon points="0,255 525,255 525,258 0,258" fill="#1f5fb0"/>
    </svg>

    <div class="front-brand">
      <div class="brand-name">SUMMIT RIDGE ESTATES</div>
      <div class="brand-slogan">"Investing in Our Community"</div>
    </div>

    <div class="holder">
      <div class="holder-name">DALE HARWICK</div>
      <div class="holder-role">Managing Member</div>
    </div>

    <address class="address" style="font-style:normal">
      4821 Corliss Pkwy ste 207-300<br>
      N. Las Vegas, NV 89084
    </address>

    <ul class="contacts">
      <li><svg viewBox="0 0 10 10"><path d="M2 0.5 L3.6 2.6 L2.8 3.6 Q4 6 6.4 7.2 L7.4 6.4 L9.5 8 L8.4 9.5 Q3 9 0.5 1.6 Z"/></svg>(702) 555-0143</li>
      <li><svg viewBox="0 0 10 10"><rect x="2.5" y="0.5" width="5" height="3"/><rect x="0.5" y="4" width="9" height="4.5" rx="1"/></svg>(702) 555-0187</li>
      <li><svg viewBox="0 0 10 10"><polygon points="0.5,4.5 9.5,0.5 6,9.5 4.8,5.6"/></svg>SummitRidgeEstate@hollowmail.test</li>
      <li><svg viewBox="0 0 10 10"><circle cx="5" cy="5" r="4.3" fill="none" stroke="#fff" stroke-width="1.2"/><path d="M0.8 5 H9.2 M5 0.8 V9.2" stroke="#fff" stroke-width="0.9"/></svg>www.SummitRidgeEstates.test</li>
    </ul>

    <p class="tagline">We buy houses for cash....no repairs, no commissions, no fees!</p>
  </section>

</div>
</body>
</html>
```